RB Halden Electric Yard Sign

Looking to have a yard sign designed that we can place at projects we are working on. Most likely will be 18" H x 24" W but flexible that we can increase the size if necessary. It should include our logo, our phone # 609-555-0147, website rbhaldenelectric.example and slogan, Wired with Care, Powered by Pride. Colors should match our brand.

```html
<!DOCTYPE html>
<html lang="en">
<head>
<meta charset="utf-8">
<title>RB Halden Electric Yard Sign</title>
<link href="https://fonts.googleapis.com/css2?family=Lexend:wght@500;600;700&display=swap" rel="stylesheet">
<style>
  :root {
    --brand-red: #e8262b;
    --brand-navy: #1a3563;
    --sign-white: #ffffff;
    --backdrop: #eef0f2;
  }
  html, body {
    margin: 0;
    padding: 0;
    width: 1200px;
    height: 877px;
    overflow: hidden;
    background: var(--backdrop);
  }
  .canvas {
    position: relative;
    width: 1200px;
    height: 877px;
    font-family: "Lexend", sans-serif;
  }
  .yard-sign {
    position: absolute;
    left: 80px;
    top: 77px;
    width: 1040px;
    height: 722px;
    background: var(--brand-red);
    box-shadow: 0 6px 18px rgba(0,0,0,0.12);
  }
  .sign-face {
    position: absolute;
    left: 14px;
    top: 14px;
    right: 14px;
    height: 621px;
    background: var(--sign-white);
  }
  .wordmark {
    position: absolute;
    left: 0;
    right: 0;
    top: 150px;
    text-align: center;
    font-weight: 700;
    font-size: 70px;
    line-height: 1;
    letter-spacing: 3px;
    text-transform: uppercase;
    color: var(--brand-red);
  }
  .trade-line {
    position: absolute;
    left: 0;
    right: 0;
    top: 262px;
    text-align: center;
    font-weight: 600;
    font-size: 36px;
    line-height: 1;
    letter-spacing: 7px;
    color: var(--brand-navy);
  }
  .trade-rule {
    position: absolute;
    left: 120px;
    top: 308px;
    width: 772px;
    height: 8px;
  }
  .phone {
    position: absolute;
    left: 0;
    right: 0;
    top: 372px;
    text-align: center;
    font-weight: 700;
    font-size: 122px;
    line-height: 1;
    color: var(--brand-navy);
  }
  .website {
    position: absolute;
    left: 0;
    right: 0;
    top: 522px;
    text-align: center;
    font-weight: 600;
    font-size: 44px;
    line-height: 1;
    color: var(--brand-navy);
  }
  .divider {
    position: absolute;
    left: 0;
    right: 0;
    top: 600px;
    height: 5px;
    background: var(--brand-navy);
  }
  .slogan-band {
    position: absolute;
    left: 0;
    right: 0;
    top: 635px;
    height: 87px;
    display: flex;
    align-items: center;
    justify-content: center;
    color: var(--sign-white);
    font-weight: 600;
    font-size: 41px;
    line-height: 1;
  }
</style>
</head>
<body>
  <main class="canvas">
    <section class="yard-sign" aria-label="RB Halden Electric yard sign">
      <div class="sign-face">
        <div class="wordmark">RB Halden Electric</div>
        <div class="trade-line">Electrical Contractor</div>
        <svg class="trade-rule" viewBox="0 0 772 8" aria-hidden="true">
          <line x1="0" y1="2" x2="772" y2="2" stroke="var(--brand-red)" stroke-width="3"/>
          <line x1="20" y1="6" x2="752" y2="6" stroke="var(--brand-navy)" stroke-width="3"/>
        </svg>
        <div class="phone">609-555-0147</div>
        <div class="website">www.rbhaldenelectric.example</div>
        <div class="divider"></div>
      </div>
      <div class="slogan-band">Wired with Care, Powered by Pride.</div>
    </section>
  </main>
</body>
</html>
```